Ecological Cosmetics (w/ Social Impact) Website

Dr. Wendelin Marovitz Naturprodukte KELVORA®, a small family-run ecological cosmetics “start-up” business (has been around since the mid 90s but only now beginning professionalize management), wishes to redesign its web presence, as part of a comprehensive “facelift” that will also encompass at a later stage its corporate identity (e.g. logo…).
We would like to prepare a new trilingual (later 3 additional languages will be added) website (www.kelvora7.at) that is symbiotic with web 2.0 enabled interwoven with a blog, news section, social networks integrated (e.g. preference/like buttons, Facebook), changing images and announcements appearing on first page, online payment services, mobile internet compatibility (e.g. iOS, Android, BlackBerry… thus no use of Flash, no need for a specific app), etc. and all the other significant trends in the e-commerce realm. The website should be easily and quickly accessible, fun to navigate, allow us to update it simply (through a content manager) and so “sexy” that people will want to return to the web, inform themselves of events and news, and hopefully also try our products.
Our company is based in Austria and specializes in the production of organic cosmetics in the mid-upper pricing range. We pride ourselves in offering natural cosmetics (the meaning of “natural” is relative and each person may have a different definition), with no petrochemical preservatives. Some of our products, such as the mineral salts and black mud powder from the Dead Sea cannot be obtained more naturally, unless you actually visit the area, thus retain all their properties. Our products are not medicine but the basic Dead Sea ingredients are used by spas and clinics in the area to treat many different skin, joint and bone affections. Our male and female customers (no distinction made will be made on our new website), primarily as of the ages of 25 to 65, buy KELVORA® because they:
• Care about the exterior and interior well-being
• Wish to look well cared, preserve their skin’s flexibility, natural splendor & properties
• Prefer natural skin care
• Nourish their skin with vital minerals/trace elements, protecting/treating their skin with natural ingredients
• Willing to pay more than average for natural cosmetics, looking for quality,
• Don’t mind spending about 15 minutes per week preparing a mud mask with some hot water.
• Bathe in water enriched with mineral salts
• Know or are surprised to find out that Dead Sea mud is one of the few, if not the only, naturally astringent (tenses the skin) muds in the world
• Help alleviate skin conditions (e.g. psoriasis, dermatitis, acne, eczema, pustules, oily skin ...), joint (e.g. rheumatism, arthritis ...) and cardiovascular disease.
Amongst the minerals in many of our products (particularly salt, mud), are sulfur and zinc, two naturally disinfecting and healing minerals, thus their common use in many dermatological drugs. Both salt and mud powder are completely natural, and without chemicals additives, quite important when dealing with sensitive or problematic skin, which reacts allergically to certain types of substances. The KELVORA line blends in both ingredients, enriching them with the highest-quality vitamins, essential oils and exceptional plant oils. Many of the competitors creams today use common ingredients such as petrolatum, paraffin (paraffinum liquidum), mineral oil, among others, which are derived from oil, are cheap ingredients (higher margins!) and clog pores!
To underline that this is not a chimera, there are quite a few researchers/scientists/doctors who have written articles about the benefits of the Dead Sea and its naturally occurring substances. Below are some links to abstracts of research papers, which are helpful in understanding the therapeutic potential of the black mud powder and mineral salt:
http://onlinelibrary.wiley.com/doi/10.1111/j.1365-4362.1995.tb03599.x/abstract
http://onlinelibrary.wiley.com/doi/10.1111/j.1365-4632.2005.02079.x/full
http://onlinelibrary.wiley.com/doi/10.1046/j.1365-4362.1997.00204.x/abstract
http://ard.bmj.com/content/49/2/99.short
http://www.springerlink.com/content/pv46n2p1m9p3k131/
http://onlinelibrary.wiley.com/doi/10.1111/j.1365-4632.2005.02621.x/full
http://journals.lww.com/jclinrheum/Abstract/2002/08000/Therapy_With_Mud_Compresses_for_Knee.3.aspx
http://onlinelibrary.wiley.com/doi/10.1111/j.1468-3083.1997.tb00509.x/abstract
http://onlinelibrary.wiley.com/doi/10.1046/j.1529-8019.2003.01622.x/full
http://onlinelibrary.wiley.com/doi/10.1046/j.1365-4362.1999.00583.x/full
The following links lead you to KELVORA® product data, mineral characteristics and a video of how to prepare a facial mud mask:
http://www.kelvora7.at/descargaanalisis.htm
http://www.kelvora7.at/estudio.htm
http://www.clipverse.example/watch?v=Qm4TzLp8WxR
We would like to convey, through our striking and attractive new graphic design, our values to potential clients: quality, 100% natural product, effectiveness, seriousness, confidence, respect for the environment, people, animals (the products are not tested on animals), all of which has a price (they are not cheap!). To put our money where our mouth is and contribute to transforming our planet into a better place, we are discussing with NGOs donating a percentage of certain product sales to support their causes.
Our web currently is available in 3 languages: German, Spanish and English, however, we plan to expand it by another 2 to 3 languages (Portuguese, Russian, Chinese). We are looking for a graphic design that will communicate our values and captivate people's attention, thereby helping us increase sales, projecting a solid and elegant image of reliability, effectiveness, simplicity and trust. Although we are not, and do not wish to, market our products as medicine, we do want to express, through our new graphic design, the fact that these products can be used to treat all types of skin, mitigate certain skin affections (e.g. psoriasis, dermatitis, acne, eczema, sensitive skin), and, depending on each organism’s reaction, different ailments (e.g. arthritis, rheumatism), although they won’t cure them (they can alleviate!).
To get an idea of our company, I invite you to explore our website, www.kelvora7.at, and see photos of our products. Attached please find some photos of our products, including the newly designed black mud powder box. We would like to create a unified corporate image. At this point we know that some, if not all, packages do not convey quality nor our values – this is something we wish to gradually change as each products’ graphic design and packaging gets renewed, consistent with the new brand image. This is work-in-progress and will be addressed as the company grows and has the financial capacity to invest in new design and packaging. We are advancing step by step.
Content-wise, we would provide you with product photos, and the texts to be inserted, but would like to complement these with other photos (e.g. from photobanks that include images of the Dead Sea, beaches, plants, nature…). The design should quickly associate the Internet user/visitor of our website with our values and the idea of quality products. A content manager will be used to update and modify our product portfolio.
Although some people will find us by typing into their web browser the address of our website, many will use search engines to locate us on the WWW. For this purpose, it would also be important that kelvora7.at’s different webpages can be referenced, searched for keywords and allow analysis of webtraffic (e.g. Google Analytics…).
Two colors are being used in our packages, green Pantone No. 326 and blue Pantone No. 072. We are completely flexible in terms of colors.
We hope you find the project interesting. Any questions, please do not hesitate to contact us. Thank you very much for your time, recommendations and proposals. Ideally we can close this project in about 14 days.
Information to be considered and/or included in the design:
• The web will feature an e-commerce shop, whose design should also be included in your creative proposal.
• Cosmetics tend to be divided along the lines of skin types, yet as the KELVORA line is still quite small, we have decided to divide it along treatment areas: hair, face, body. Each product is indicated for a particular skin type.
• Keyword Search box for the entire website
The current web is slow, all in Flash, difficult to navigate, has too many intermediate stages, does not offer a keyword search function, nor incorporate any web 2.0 features. Furthermore, it is more difficult to find and index in search engines as none of the pages have specific web addresses. In terms of intermediate pages, these should be eliminated shortening the time the user needs to obtain the desired information (e.g. the landing page where you choose sex & language, followed by drop of water being filled up), such that the visitor is directly lead to the main page (equal to the landing page). At first glance, the blue background and the drop of water filling up may lead the visitor to believe we are dedicated to something with water, perhaps even plumbing or purification services – such an impression must be avoided. Perhaps one of the ways to analyze all the aspects to be incorporated is an evaluation of our current web’s weaknesses and prepare a design where those are all addressed.
Target Market(s)
Male & female customers, approx. age 18-65, who care about their exterior and interior well being, “worried” about their skin, willing to pay more tha
Industry/Entity Type
Graphic Design
Requirements
Must have
- • The web will also feature a blog and an e-commerce shop, whose designs should also be included in your creative proposal.
• Address current and future languages
Content-wise, we will product photos, and the texts to be inserted, but would like to complement these with other photos (e.g. from photobanks that include images of the Dead Sea, beaches, plants, nature…). The design should quickly associate the Internet user/visitor of our website with our values and the idea of quality products. A content manager will be used to update and modify our product portfolio, as well as effects announcements on the landing page.

```html
<!DOCTYPE html>
<html lang="en">
<head>
<meta charset="utf-8">
<title>KELVORA® Naturprodukte</title>
<link rel="stylesheet" href="https://fonts.googleapis.com/css2?family=Open+Sans:wght@300;400;600;700&family=Roboto+Condensed:wght@400;700&display=swap">
<style>
:root{
  --nav-cyan:#1aa6e0;
  --feed-blue:#1a8cc4;
  --navy:#3e4c80;
  --brand-navy:#12236b;
  --leaf:#a8c91f;
  --ink:#222;
  --muted:#8a8a8a;
  --btn:#333;
  --panel:#f1f1f1;
  --line:#b8b8b8;
  --link-red:#d4361f;
}
*{box-sizing:border-box;margin:0;padding:0}
html,body{width:1050px;height:1200px;overflow:hidden;background:#fff}
body{font-family:"Open Sans",Arial,sans-serif;color:var(--ink);position:relative}
.page{position:absolute;left:13px;top:10px;width:1024px;height:1180px}
.abs{position:absolute}

.lang{left:932px;top:14px;font-family:"Roboto Condensed",Arial,sans-serif;font-size:12px;color:#666}
.lang b{color:#000;font-weight:400}

.brand-dot{left:36px;top:60px;width:20px;height:20px;border-radius:50%;background:var(--leaf)}
.main-nav{left:0;top:87px;width:1024px;height:18px}
.main-nav a{position:absolute;font-family:"Roboto Condensed",Arial,sans-serif;font-size:13px;color:var(--nav-cyan);text-decoration:none;letter-spacing:.1px}

.hero{left:11px;top:115px;width:1002px;height:400px;border:1px solid #e2e2e2;box-shadow:0 0 6px rgba(0,0,0,.06);background:#fff;overflow:hidden}
.hero-photo{position:absolute;left:450px;top:10px;width:540px;height:380px;
  background:radial-gradient(ellipse at 62% 48%,#f0c9ad 0%,#e8b899 22%,#f3ece8 48%,rgba(255,255,255,0) 75%),
  linear-gradient(90deg,#fff 0%,#fafafa 40%,#eeeeee 100%)}
.brand-mark{position:absolute;left:222px;top:150px;display:flex;align-items:center;gap:10px}
.brand-mark .dot{width:26px;height:26px;border-radius:50%;background:var(--brand-navy)}
.brand-mark span{font-weight:700;font-size:24px;color:var(--brand-navy);letter-spacing:.5px}
.hero-text{position:absolute;left:30px;top:270px;width:560px;font-size:17.5px;line-height:22px;color:var(--navy)}

.section-title{left:35px;top:540px;font-family:"Open Sans",sans-serif;font-weight:300;font-size:25px;color:var(--navy);letter-spacing:.2px}

.products{left:36px;top:576px;width:629px;height:393px;border:1px solid #a0a0a0;border-radius:6px}
.product{position:absolute;width:160px;text-align:center}
.product .shot{width:153px;height:95px;margin:0 auto}
.product .name{font-size:11px;margin-top:10px;color:#222}
.product .actions{display:flex;gap:4px;justify-content:center;margin-top:7px}
.btn{width:74px;height:27px;border-radius:3px;background:linear-gradient(#474747,#2b2b2b);color:#fff;font-size:10.5px;line-height:27px;text-align:center}
.divider{position:absolute;left:22px;top:199px;width:582px;height:1px;background:var(--line)}

.pager{left:37px;top:999px;width:620px;height:38px;background:#f3f3f3;font-size:12px;color:#555;text-align:right;padding-right:16px;line-height:38px;word-spacing:6px}

.feeds{left:687px;top:575px;width:299px;height:331px;background:var(--panel);border-radius:8px}
.feeds-title{position:absolute;left:100px;top:14px;font-size:13px;font-weight:700;color:var(--feed-blue)}
.feeds-dot{position:absolute;left:64px;top:15px;width:18px;height:14px;border-radius:50%;background:var(--feed-blue)}
.feeds-arrow{position:absolute;left:272px;top:14px}
.tweet{position:absolute;left:20px;width:270px}
.tweet .avatar{position:absolute;left:0;top:0;width:96px;height:122px;background:linear-gradient(135deg,#6b4a33,#d9ad93 45%,#c9937a 70%,#5a3e2c)}
.tweet p{position:absolute;left:115px;top:0;width:145px;font-size:11.2px;line-height:22px;color:var(--muted)}
.tweet p a{color:var(--link-red);text-decoration:none}

.search-title{left:726px;top:929px;font-size:16px;color:var(--navy)}
.search-icon{left:694px;top:928px}
.search-box{left:703px;top:964px;width:260px;height:38px;border:1px solid #cfcfcf;box-shadow:inset 0 1px 3px rgba(0,0,0,.12);background:#fff}
.search-box .ph{position:absolute;left:13px;top:12px;font-size:12px;font-style:italic;color:#999}
.search-box .go{position:absolute;left:210px;top:5px;width:44px;height:27px;border-radius:3px;background:#333;color:#fff;font-size:12px;font-style:italic;text-align:center;line-height:27px}

.footer{left:590px;top:1091px;font-size:9.3px;line-height:18px;color:#777}
</style>
</head>
<body>
<div class="page">
  <div class="abs lang"><b>EN</b> | DE | ES</div>

  <div class="abs brand-dot"></div>
  <nav class="abs main-nav">
    <a style="left:20px">HOME</a>
    <a style="left:112px">KELVORA</a>
    <a style="left:211px">DEAD SEA</a>
    <a style="left:323px">AROMATHERAPY</a>
    <a style="left:471px">FACIAL CARE</a>
    <a style="left:600px">BODY CARE</a>
    <a style="left:721px">HAIR CARE</a>
    <a style="left:837px">SPAS</a>
    <a style="left:926px">CONTACT</a>
  </nav>

  <section class="abs hero">
    <div class="hero-photo" role="img" aria-label="Photo of a woman with a white towel wrapped on her head holding a white calla lily"></div>
    <div class="brand-mark"><div class="dot"></div><span>KELVORA®</span></div>
    <p class="hero-text">Lorem ipsum dolor sit amet, consectetur adipiscing elit. Etiam vel rutrum elit. Duis elit quam, eleifend eget sollicitudin sed, sodales vitae tortor.</p>
  </section>

  <h2 class="abs section-title">OUR PRODUCTS</h2>

  <section class="abs products">
    <div class="product" style="left:28px;top:21px">
      <div class="shot" role="img" aria-label="Product photo: cold cream jar with box" style="background:linear-gradient(90deg,#e8e8e8,#f4f4f4 50%,#cfe0dc)"></div>
      <div class="name">Duis aute irure dolor</div>
      <div class="actions"><div class="btn">View more</div><div class="btn">Buy this</div></div>
    </div>
    <div class="product" style="left:231px;top:21px">
      <div class="shot" role="img" aria-label="Product photo: green shampoo bottle" style="background:radial-gradient(ellipse 14% 48% at 50% 52%,#7cc23a 0%,#8bcb45 80%,rgba(255,255,255,0) 100%)"></div>
      <div class="name">Duis aute irure dolor</div>
      <div class="actions"><div class="btn">View more</div><div class="btn">Buy this</div></div>
    </div>
    <div class="product" style="left:434px;top:21px">
      <div class="shot" role="img" aria-label="Product photo: dark perfume bottle" style="background:radial-gradient(ellipse 12% 42% at 50% 48%,#3a2438 0%,#5a2a56 70%,rgba(255,255,255,0) 100%)"></div>
      <div class="name">Duis aute irure dolor</div>
      <div class="actions"><div class="btn">View more</div><div class="btn">Buy this</div></div>
    </div>

    <div class="divider"></div>

    <div class="product" style="left:28px;top:220px">
      <div class="shot" role="img" aria-label="Product photo: green and white skincare bottles with foundation tube" style="background:radial-gradient(ellipse 45% 50% at 45% 50%,#d7e8b8 0%,#e6d2c0 70%,rgba(255,255,255,0) 100%)"></div>
      <div class="name">Duis aute irure dolor</div>
      <div class="actions"><div class="btn">View more</div><div class="btn">Buy this</div></div>
    </div>
    <div class="product" style="left:231px;top:220px">
      <div class="shot" role="img" aria-label="Product photo: white cream tubes with green labels" style="background:radial-gradient(ellipse 26% 50% at 50% 50%,#e6ecd6 0%,#eeeeee 70%,rgba(255,255,255,0) 100%)"></div>
      <div class="name">Duis aute irure dolor</div>
      <div class="actions"><div class="btn">View more</div><div class="btn">Buy this</div></div>
    </div>
    <div class="product" style="left:434px;top:220px">
      <div class="shot" role="img" aria-label="Product photo: orange-themed product range with boxes and a glass" style="background:radial-gradient(ellipse 48% 50% at 50% 55%,#f3c9a0 0%,#f1e4d8 70%,rgba(255,255,255,0) 100%)"></div>
      <div class="name">Duis aute irure dolor</div>
      <div class="actions"><div class="btn">View more</div><div class="btn">Buy this</div></div>
    </div>
  </section>

  <div class="abs pager">Front&nbsp;&lt;&lt;&nbsp; 1 2 3 4 . . . . 8 9 10 &nbsp;&gt;&gt;&nbsp;Last</div>

  <aside class="abs feeds">
    <div class="feeds-dot"></div>
    <div class="feeds-title">CHIRPLINE FEEDS</div>
    <svg class="feeds-arrow" width="14" height="14" viewBox="0 0 14 14" aria-hidden="true"><path d="M1 7h9M6 2l5 5-5 5" fill="none" stroke="#444" stroke-width="2.4"/></svg>
    <div class="tweet" style="top:48px">
      <div class="avatar" role="img" aria-label="Profile photo"></div>
      <p>The first release in a series of themes that will be available on the Motif Grove - Tessro PageLoom Theme<br><a>http://snip.example/ihfm3L</a></p>
    </div>
    <div class="tweet" style="top:189px">
      <div class="avatar" role="img" aria-label="Profile photo"></div>
      <p>The first release in a series of themes that will be available on the Motif Grove - Tessro PageLoom Theme<br><a>http://snip.example/ihfm3L</a></p>
    </div>
  </aside>

  <svg class="abs search-icon" width="22" height="22" viewBox="0 0 22 22" aria-hidden="true"><circle cx="8" cy="8" r="6" fill="#9a9a9a"/><path d="M12 12l7 7" stroke="#8a8a8a" stroke-width="4" stroke-linecap="round"/></svg>
  <div class="abs search-title">PRODUCT SEARCH</div>
  <div class="abs search-box"><span class="ph">Product Name</span><div class="go">GO</div></div>

  <footer class="abs footer">
    Copyright ©2012 by KELVORA NATURPRODUKTE DR. WENDELIN MAROVITZ. All rights reserved.<br>
    www.kelvora7.at &nbsp; Email: info@kelvora7.at<br>
    Visit KELVORA® and learn more about the skin
  </footer>
</div>
</body>
</html>
```